Design a Job Application & CV

I need a design for upcoming job applications that includes a cv. It needs to look as elegant and modern as possible as the application will be send mainly to large corporations and strategy consultancies. I have attached an application that I like for your consideration. One of the more difficult requirements is that it needs to be editable in ms office word for mac/windows.
As stated only the design is part of this project. I will fill in my content later on.
Reason: Dear Designers,
I am going to increase the budget as well as extending the deadline. I am hoping that you can improve upon the design that I have provided in the brief. If you have questions please let me know.
Dear Designers,
Target Market(s)
Human Resources Managers, Senior Consultants and Executives of larger firms
Industry/Entity Type
Office
Requirements
Must have
- 4 Pages including( a cover page, a coverletter page, 2 pages cv)
It should be easy to edit and should be readable by word for mac, i.e. in the *.docx format.
Here is an example of what I like:
http://www.torvenmald.example/applicationexample.pdf
http://www.torvenmald.example/applicationExample.docx
colors that I like are blue, grey, black, white
Nice to have
- icons to indicate sections
Should not have
- invasive cliparts

```html
<!DOCTYPE html>
<html lang="en">
<head>
<meta charset="utf-8">
<title>Coverletter</title>
<link rel="stylesheet" href="https://fonts.googleapis.com/css2?family=Jura:wght@400&family=Crimson+Text:wght@400&display=swap">
<style>
  :root {
    --brand-blue: #1499d3;
    --brand-grey: #6d6e72;
    --ink: #1a1a1a;
    --paper: #ffffff;
    --edge: #d6d6d6;
  }
  * { margin: 0; padding: 0; box-sizing: border-box; }
  html, body { width: 848px; height: 1200px; overflow: hidden; background: var(--paper); }
  .letter-page {
    position: relative;
    width: 848px;
    height: 1200px;
    background: var(--paper);
    border-left: 1px solid var(--edge);
    overflow: hidden;
  }
  .header-band, .footer-band { position: absolute; left: 0; display: block; }
  .header-band { top: 0; }
  .footer-band { bottom: 0; }
  .page-title {
    position: absolute;
    left: 33px;
    top: 18px;
    font-family: "Jura", sans-serif;
    font-weight: 400;
    font-size: 50px;
    line-height: 1;
    letter-spacing: 0.02em;
    color: var(--paper);
  }
  .letter-body {
    position: absolute;
    left: 47px;
    top: 206px;
    width: 755px;
    font-family: "Crimson Text", serif;
    font-size: 18.5px;
    line-height: 31.3px;
    letter-spacing: 0.06em;
    color: var(--ink);
  }
  .letter-meta {
    display: flex;
    justify-content: space-between;
    margin-bottom: 67px;
  }
  .letter-text p {
    text-align: justify;
    hyphens: auto;
    margin-bottom: 31.3px;
  }
  .letter-text p:last-child { margin-bottom: 27px; }
  .letter-signoff { line-height: 31.3px; }
</style>
</head>
<body>
<main class="letter-page">
  <svg class="header-band" width="848" height="97" viewBox="0 0 848 97" aria-hidden="true">
    <polygon points="0,0 637,0 617,97 0,97" fill="var(--brand-blue)"/>
    <polygon points="645,0 848,0 848,97 625,97" fill="var(--brand-grey)"/>
  </svg>
  <h1 class="page-title">Coverletter</h1>

  <section class="letter-body">
    <div class="letter-meta">
      <span class="salutation">Dear folks,</span>
      <span class="letter-date">Date : 08.06.2011</span>
    </div>
    <div class="letter-text">
      <p>Lorem ipsum dolor sit amet, consectetur adipiscing elit. Quisque dictum leo quis mauris dictum auctor. Praesent viverra, elit at rutrum fringilla, purus nisi feugiat est, sit amet lobortis magna mauris id nibh. Sed interdum massa non mauris faucibus cursus. Integer at tellus sit amet lacus ultrices ullamcorper. Nunc vel libero dui, sit amet pellentesque ligula. Suspendisse semper, urna.</p>
      <p>Aenean quis nisi arcu, blandit mollis odio. Vestibulum nulla enim, viverra a auctor quis, suscipit rhoncus libero. Donec quis libero vel magna luctus pulvi&shy;nar. Duis eget nulla vel massa commodo semper placerat id leo. Nunc eu leo sed quam hendrerit accumsan. Maecenas eleifend nisi non velit dignissim ut suscipit arcu imperdiet. Phasellus nisi nulla, tincidunt. Proin tincidunt, est sed rhoncus mattis, nunc sem aliquet quam, eget tristique augue dolor vel orci. Vestibulum et tellus dui, vitae sollicitudin sapien. Pellentesque nisl tortor, faucibus in mollis non, dignissim et felis.</p>
      <p>Phasellus nisi nulla, tincidunt. Proin tincidunt, est sed rhoncus mattis, nunc sem aliquet quam, eget tristique augue dolor vel orci. Vestibulum et tellus dui, vitae sollicitudin sapien. Pellentesque nisl tortor, faucibus in mollis non, dign&shy;issim et felis.</p>
    </div>
    <p class="letter-signoff">Sincerely,<br>Good Looking</p>
  </section>

  <svg class="footer-band" width="848" height="31" viewBox="0 0 848 31" aria-hidden="true">
    <polygon points="0,0 210,0 225,31 0,31" fill="var(--brand-grey)"/>
    <polygon points="217,0 848,0 848,31 232,31" fill="var(--brand-blue)"/>
  </svg>
</main>
</body>
</html>
```